Kickbut Home Page Design built to Sell

We need a new home page layout. The website is working now but we need a refresh. Our business has slowed down since a few years ago. We need to show we build ecommerce and membership websites. Here is the page now: https://www.brelvoxstudio.graphics/new-home/

Target Market(s)

Women, solopreneurs, artists, politicians

Industry/Entity Type

Design Agency

Number of Pages Required

1 page

Font styles to use
Sans Serif

Colors
b8a6cd
fabb94
acd136
00a990

Requirements
Must have
• Video header
Section for text and Step process similar to this website: https://quintarelweb.com/ [This is out sister company]
Places for images.
Call to action lead gen form and Get a quote.
The menu should show WEB, PRINT, VIDEO
Nice to have
• I LOVE this company: https://tarnwickly.com/guide/
Area for testimonials
Should not have
• We don't want a duplicate of https://quintarelweb.com/

```html
<!DOCTYPE html>
<html lang="en">
<head>
<meta charset="utf-8">
<title>Brelvox Studio – Home</title>
<link rel="stylesheet" href="https://fonts.googleapis.com/css2?family=Montserrat:wght@400;500;600&family=Roboto:ital,wght@0,400;0,500;1,400&family=Lato:wght@400&display=swap">
<style>
:root{
  --teal:#00a990;
  --lime:#acd136;
  --lavender:#b8a6cd;
  --peach:#fabb94;
  --ink:#222222;
  --text:#333333;
  --muted:#555555;
  --soft-bg:#f5f5f5;
  --footer:#272727;
  --white:#ffffff;
  --line:#cfcfcf;
}
*{box-sizing:border-box;margin:0;padding:0}
html,body{width:1200px;height:3242px;overflow:hidden}
body{position:relative;background:var(--white);font-family:'Roboto',sans-serif;color:var(--text)}
.abs{position:absolute}

/* header */
.site-header{left:0;top:0;width:1200px;height:81px;background:var(--white)}
.brand{left:112px;top:24px}
.brand-name{font-family:'Montserrat',sans-serif;font-weight:600;font-size:25px;color:var(--teal);letter-spacing:0.5px;line-height:28px}
.brand-tag{font-family:'Montserrat',sans-serif;font-weight:600;font-size:6.5px;color:var(--teal);letter-spacing:1.3px;margin-top:1px}
.main-nav{right:115px;top:34px;display:flex;gap:26px;font-family:'Montserrat',sans-serif;font-size:15px;letter-spacing:0.3px}
.main-nav a{color:var(--ink);text-decoration:none}
.main-nav a.active{color:var(--teal)}

/* hero */
.hero{left:0;top:81px;width:1200px;height:600px;background:linear-gradient(90deg,#0b0b0a 0%,#17160f 28%,#5b5a3e 48%,#8f8b66 62%,#6b5c48 78%,#3d342c 100%)}
.hero-title{left:112px;top:200px;font-family:'Montserrat',sans-serif;font-weight:600;font-size:23.5px;line-height:40px;color:var(--white);letter-spacing:0.2px}
.hero-sub{left:112px;top:286px;font-size:16px;line-height:28px;color:var(--white)}
.btn{display:flex;align-items:center;justify-content:center;border-radius:26px;font-family:'Roboto',sans-serif;font-weight:500;font-size:15px;text-decoration:none}
.btn-teal{background:var(--teal);color:var(--white)}
.btn-lime{background:var(--lime);color:#1f2a00}
.hero .quote{left:112px;top:366px;width:154px;height:51px}
.hero .work{left:275px;top:366px;width:154px;height:51px}
.play{left:870px;top:255px;width:90px;height:90px}

/* process */
.process-photo{left:0;top:681px;width:600px;height:556px;background:linear-gradient(135deg,#6d6157 0%,#a39280 40%,#8a5a48 65%,#5a4c45 100%)}
.process{left:600px;top:681px;width:600px;height:556px;background:var(--soft-bg)}
.process h2{position:absolute;left:40px;top:48px;font-family:'Montserrat',sans-serif;font-weight:500;font-size:32px;color:var(--ink);letter-spacing:0.5px}
.step{position:absolute;left:38px;width:520px}
.step-icon{position:absolute;left:0;top:0;width:64px;height:64px}
.step-one .disc{fill:var(--teal)}
.step-two .disc{fill:var(--lavender)}
.step-three .disc{fill:var(--peach)}
.step h3{position:absolute;left:75px;top:2px;font-family:'Montserrat',sans-serif;font-weight:500;font-size:19px;color:var(--ink);white-space:nowrap}
.step p{position:absolute;left:76px;top:38px;width:420px;font-size:13.5px;line-height:25px;color:var(--muted)}
.process .quote{position:absolute;left:43px;top:447px;width:154px;height:52px;box-shadow:0 3px 6px rgba(0,0,0,.2)}

/* gallery */
.section-title{width:1200px;text-align:center;font-family:'Montserrat',sans-serif;font-weight:600;font-size:40px;color:var(--ink);letter-spacing:0.5px}
.gallery-title{left:0;top:1312px}
.gallery-item{width:317px;height:256px;box-shadow:0 1px 4px rgba(0,0,0,.15)}

/* testimonials */
.testimonials{left:0;top:1995px;width:1200px;height:341px;background:linear-gradient(180deg,#0aa78d,#05a088)}
.testimonials h2{position:absolute;left:0;top:32px;width:1200px;text-align:center;font-family:'Montserrat',sans-serif;font-weight:600;font-size:41px;color:var(--white)}
.quote-text{position:absolute;left:152px;top:103px;width:896px;text-align:center;font-style:italic;font-size:15.5px;line-height:30px;color:var(--white)}
.author{position:absolute;left:0;top:245px;width:1200px;text-align:center;color:var(--white);font-weight:500;font-size:20px}
.author-role{position:absolute;left:0;top:277px;width:1200px;text-align:center;color:var(--white);font-size:16px}

/* contact */
.contact-title{left:-6px;top:2413px}
.field{border:1px solid var(--line);background:var(--white);font-family:'Lato',sans-serif;font-size:15px;color:#777;padding:18px 10px}
.submit{left:190px;top:2792px;width:820px;height:57px;background:var(--teal);color:var(--white);font-family:'Montserrat',sans-serif;font-weight:600;font-size:21px;display:flex;align-items:center;justify-content:center;letter-spacing:0.5px}

/* footer */
.site-footer{left:0;top:2934px;width:1200px;height:253px;background:var(--footer)}
.contact-line{position:absolute;left:0;width:1200px;display:flex;justify-content:center;align-items:center;gap:6px;color:var(--white);font-size:18.5px}
.socials{position:absolute;left:506px;top:180px;display:flex;gap:12px}
.social{width:38px;height:36px;border:1px solid var(--white);display:flex;align-items:center;justify-content:center}
.footer-bar{left:0;top:3187px;width:1200px;height:55px;background:var(--teal);color:var(--white);font-size:15.5px}
.footer-links{position:absolute;left:112px;top:17px;display:flex;gap:24px}
.copyright{position:absolute;right:112px;top:17px}
</style>
</head>
<body>

<header class="site-header abs">
  <div class="brand abs">
    <div class="brand-name">BRELVOXSTUDIO</div>
    <div class="brand-tag">GRAPHICS WEB VIDEO CONSULTANTS</div>
  </div>
  <nav class="main-nav abs">
    <a class="active" href="#">HOME</a><a href="#">WEB</a><a href="#">PRINT</a><a href="#">VIDEO</a>
  </nav>
</header>

<section class="hero abs" role="img" aria-label="Video header: a designer leaning over a desktop computer in a bright studio">
  <h1 class="hero-title abs">LEAD GENERATING WEBSITES THAT<br>MOVE YOUR BUSINESS FORWARD</h1>
  <p class="hero-sub abs">Your Company Deserves a Website That Can Inspire<br>People To Take Action</p>
  <a class="btn btn-teal quote abs" href="#">Get Free Quote</a>
  <a class="btn btn-lime work abs" href="#">View Our Work</a>
  <svg class="play abs" viewBox="0 0 90 90" aria-label="Play video">
    <circle cx="45" cy="45" r="45" fill="#00a990"/>
    <path d="M36 31 L60 45 L36 59 Z" fill="#fff"/>
  </svg>
</section>

<div class="process-photo abs" role="img" aria-label="Photo of a team meeting around a low table with laptops"></div>
<section class="process abs">
  <h2>THE PROCESS IS SIMPLE</h2>
  <div class="step step-one" style="top:128px">
    <svg class="step-icon" viewBox="0 0 64 64"><circle class="disc" cx="32" cy="32" r="32"/><g fill="none" stroke="#fff" stroke-width="2.6" stroke-linecap="round" stroke-linejoin="round"><path d="M30 21h-8a2 2 0 0 0-2 2v19a2 2 0 0 0 2 2h19a2 2 0 0 0 2-2v-8"/><path d="M39 18l6 6-12 12h-6v-6z"/></g></svg>
    <h3>Step 1 - Tell Us Your Needs</h3>
    <p>Tell us about your online store, membership area or sales goals</p>
  </div>
  <div class="step step-two" style="top:231px">
    <svg class="step-icon" viewBox="0 0 64 64"><circle class="disc" cx="32" cy="32" r="32"/><g fill="none" stroke="#fff" stroke-width="2.4" stroke-linecap="round" stroke-linejoin="round"><path d="M22 20c-3 3-3 8 2 15s12 11 16 9l3-3-5-5-3 2c-3-1-6-5-7-8l2-3-5-5z"/><path d="M34 22a8 8 0 0 1 8 8"/><path d="M34 16a14 14 0 0 1 14 14"/></g></svg>
    <h3>Step 2 - Phone Call</h3>
    <p>We talk through products, payments, member levels and the features you need</p>
  </div>
  <div class="step step-three" style="top:334px">
    <svg class="step-icon" viewBox="0 0 64 64"><circle class="disc" cx="32" cy="32" r="32"/><g fill="#fff"><path d="M26 20h12v4h-3v-1h-6v1h-3z"/><rect x="17" y="24" width="30" height="8" rx="1.5"/><rect x="17" y="34" width="30" height="11" rx="1.5"/></g></svg>
    <h3>Step 3 - Custom Quote Arrives</h3>
    <p>A clear quote arrives for your ecommerce or membership website, with timeline and every detail</p>
  </div>
  <a class="btn btn-teal quote" href="#">Get Free Quote</a>
</section>

<h2 class="section-title gallery-title abs">OUR GALLERY</h2>
<div class="gallery-item abs" style="left:112px;top:1386px;background:linear-gradient(135deg,#4a4844,#9a9a98 60%,#d8d8d4)" role="img" aria-label="Gallery photo: team reviewing work at a desktop computer"></div>
<div class="gallery-item abs" style="left:441px;top:1386px;background:linear-gradient(135deg,#cfcac4,#6c5a4e 50%,#d9d6d2)" role="img" aria-label="Gallery photo: smiling group looking at printed designs"></div>
<div class="gallery-item abs" style="left:771px;top:1386px;background:linear-gradient(180deg,#f2f2f0,#e0e0de 70%,#b9b7b3)" role="img" aria-label="Gallery photo: online store website shown on desktop, laptop, tablet and phone"></div>
<div class="gallery-item abs" style="left:112px;top:1653px;background:linear-gradient(135deg,#a8a49c,#5b5650 50%,#2f3034)" role="img" aria-label="Gallery photo: colleagues building a membership site at laptops"></div>
<div class="gallery-item abs" style="left:441px;top:1653px;background:linear-gradient(135deg,#5c5a58,#a39f9a 50%,#4a6c78)" role="img" aria-label="Gallery photo: designers choosing colour swatches"></div>
<div class="gallery-item abs" style="left:771px;top:1653px;background:linear-gradient(135deg,#ece9e4,#a14a43 35%,#d9d8d6 70%,#9aa3b0)" role="img" aria-label="Gallery photo: planning session at a whiteboard"></div>

<section class="testimonials abs">
  <h2>TESTIMONIALS</h2>
  <p class="quote-text">Dana Whitfield was great to work with and extremely knowledgeable and accessible. I especially appreciated his well thought out design process and the client videos he created to walk me through various stages of it. I received lots of great feedback on the visual look, user-friendliness, and rich content of my website throughout the campaign and was re-elected overwhelmingly. I highly recommend Dana and Quintarel Web for your next project!</p>
  <div class="author">MARTIN OSLOWE</div>
  <div class="author-role">MAYOR, ASHFORD FALLS, MA</div>
</section>

<h2 class="section-title contact-title abs">CONTACT US</h2>
<form>
  <div class="field abs" style="left:190px;top:2492px;width:402px;height:58px">Name</div>
  <div class="field abs" style="left:608px;top:2492px;width:402px;height:58px">Surname</div>
  <div class="field abs" style="left:190px;top:2566px;width:402px;height:58px">Email</div>
  <div class="field abs" style="left:608px;top:2566px;width:402px;height:58px">Phone</div>
  <div class="field abs" style="left:190px;top:2642px;width:820px;height:136px">Message</div>
  <div class="submit abs">SUBMIT</div>
</form>

<footer class="site-footer abs">
  <div class="contact-line" style="top:54px">
    <svg width="12" height="17" viewBox="0 0 12 17"><path d="M6 0a6 6 0 0 0-6 6c0 4.5 6 11 6 11s6-6.5 6-11a6 6 0 0 0-6-6zm0 8.5A2.5 2.5 0 1 1 6 3.5a2.5 2.5 0 0 1 0 5z" fill="#00a990"/></svg>
    <span>18 Fenmore Ave, Lakeport MA 01999</span>
  </div>
  <div class="contact-line" style="top:87px">
    <svg width="15" height="15" viewBox="0 0 16 16"><path d="M3.5 1l3 3-2 2.2c1 2.2 2.6 3.8 4.8 4.8L11.5 9l3 3-2 2.6C7.5 14.5 1.5 8.5 1 3.5z" fill="#00a990"/></svg>
    <span>1-555-010-4821</span>
  </div>
  <div class="contact-line" style="top:120px">
    <svg width="18" height="13" viewBox="0 0 18 13"><rect width="18" height="13" rx="1.5" fill="#00a990"/><path d="M1 1.5l8 6 8-6" fill="none" stroke="#272727" stroke-width="1.5"/></svg>
    <span>dana@quintarelweb.com</span>
  </div>
  <div class="socials" aria-label="Social links">
    <span class="social"><svg width="14" height="14" viewBox="0 0 14 14"><circle cx="7" cy="7" r="6" fill="#fff"/></svg></span>
    <span class="social"><svg width="14" height="14" viewBox="0 0 14 14"><circle cx="7" cy="7" r="6" fill="#fff"/></svg></span>
    <span class="social"><svg width="14" height="14" viewBox="0 0 14 14"><circle cx="7" cy="7" r="6" fill="#fff"/></svg></span>
    <span class="social"><svg width="14" height="14" viewBox="0 0 14 14"><circle cx="7" cy="7" r="6" fill="#fff"/></svg></span>
  </div>
</footer>

<div class="footer-bar abs">
  <div class="footer-links"><span>Web</span><span>Print</span><span>Video</span></div>
  <div class="copyright">© 2021 Quintarel Development. All Rights Reserved. Lakeport MA 01999</div>
</div>

</body>
</html>
```